Business Card Design (NEW FILES)

ATTENTION: New vector files are available. Please update your design to reflect/use the new (better resolution) logo images.

Seeking a unique and professional business card design for a commercial drone photography/videography business. The layout should feature
the logo (attached) and include the following information:
Owen Tarrick
614-502-7738
www.skylarkreelworks.example
NRD Certified Remote Pilot

Owen Tarrick

```html
<!DOCTYPE html>
<html lang="en">
<head>
<meta charset="utf-8">
<title>Skylark Reelworks – Business Card</title>
<link href="https://fonts.googleapis.com/css2?family=Lato:wght@400;700;900&display=swap" rel="stylesheet">
<style>
  :root{
    --navy:#131a47;
    --orange:#ec8a4b;
    --white:#ffffff;
    --backdrop:#8f8f8f;
    --bar-purple:#4b2a8c;
    --bar-magenta:#c02a8f;
    --bar-red:#d8232f;
    --bar-orange:#f08a2c;
    --bar-green:#8cc63f;
    --bar-cyan:#1fb5d6;
  }
  *{margin:0;padding:0;box-sizing:border-box}
  html,body{width:1200px;height:1200px;overflow:hidden}
  body{background:var(--backdrop);font-family:'Lato',sans-serif;position:relative}
  .card{position:absolute;left:281px;width:641px;height:366px;border-radius:16px}
  .card-front{top:195px;background:var(--white)}
  .card-back{top:639px;background:var(--navy)}

  .brand{position:absolute;display:flex;align-items:center;gap:9px;font-weight:700;white-space:nowrap}
  .card-front .brand{left:62px;top:184px;width:260px;font-size:20px;letter-spacing:.4px;color:var(--navy)}
  .card-back .brand{left:0;right:0;top:160px;justify-content:center;font-size:44px;letter-spacing:1px;color:var(--white)}
  .brand-dot{border-radius:50%;background:var(--orange);flex:none}
  .card-front .brand-dot{width:12px;height:12px}
  .card-back .brand-dot{width:22px;height:22px}

  .divider{position:absolute;left:347px;top:93px;width:2px;height:181px;display:flex;flex-direction:column}
  .divider span{flex:1}

  .details{position:absolute;left:382px;top:90px;color:var(--navy)}
  .name{font-weight:900;font-size:28px;line-height:30px;letter-spacing:.3px}
  .role{color:var(--orange);font-size:18px;line-height:24px;margin-bottom:10px}
  .contact{list-style:none}
  .contact li{display:flex;align-items:center;gap:10px;font-size:15px;line-height:23px}
  .contact svg{width:12px;height:12px;fill:var(--orange);flex:none}
  .cert{margin-top:14px;font-size:15.5px;line-height:22px}
  .insured{color:var(--orange);font-weight:900;font-size:16px;letter-spacing:1px;line-height:22px}
</style>
</head>
<body>
  <section class="card card-front">
    <div class="brand"><span class="brand-dot"></span>SKYLARK REELWORKS</div>
    <div class="divider" aria-hidden="true">
      <span style="background:var(--bar-purple)"></span>
      <span style="background:var(--bar-magenta)"></span>
      <span style="background:var(--bar-red)"></span>
      <span style="background:var(--bar-orange)"></span>
      <span style="background:var(--bar-green)"></span>
      <span style="background:var(--bar-cyan)"></span>
    </div>
    <div class="details">
      <h1 class="name">OWEN TARRICK</h1>
      <p class="role">Owner</p>
      <ul class="contact">
        <li><svg viewBox="0 0 24 24"><path d="M6.6 10.8a15.1 15.1 0 0 0 6.6 6.6l2.2-2.2c.3-.3.7-.4 1-.2 1.1.4 2.3.6 3.6.6.6 0 1 .4 1 1V20c0 .6-.4 1-1 1A17 17 0 0 1 3 4c0-.6.4-1 1-1h3.5c.6 0 1 .4 1 1 0 1.3.2 2.5.6 3.6.1.3 0 .7-.2 1z"/></svg>614-502-7738</li>
        <li><svg viewBox="0 0 24 24"><path d="M2 5h20v2l-10 6L2 7z M2 9l10 6 10-6v10H2z"/></svg>owen@skylarkreelworks.example</li>
        <li><svg viewBox="0 0 24 24"><path d="M12 2a10 10 0 1 0 0 20 10 10 0 0 0 0-20zm-1 17.9A8 8 0 0 1 4.2 10L9 14.8v1c0 1.1.9 2 2 2zm6.9-2.5c-.3-.8-1-1.4-1.9-1.4h-1v-3c0-.6-.4-1-1-1H8v-2h2c.6 0 1-.4 1-1V7h2c1.1 0 2-.9 2-2v-.4a8 8 0 0 1 2.9 12.8z"/></svg>skylarkreelworks.example</li>
      </ul>
      <p class="cert">NRD Certified Remote Pilot</p>
      <p class="insured">FULLY INSURED</p>
    </div>
  </section>

  <section class="card card-back">
    <div class="brand"><span class="brand-dot"></span>SKYLARK REELWORKS</div>
  </section>
</body>
</html>
```